Sell the dream! Property investment proposal document

We are looking for a proposal document which outlines our vision for property development. The purpose of the document is to raise investment from investors - sell the dream!
Brief summary:
Kestrel Dwellings Developments, is an emerging New Zealand property investment company with a focus on providing unique property investment opportunities.
Our expertise and capabilities in architectural modular homes provide us with a remarkable advantage in tackling the development of properties that are typically considered challenging, remote, or uniquely positioned.
Our specialization in this niche sector of property development not only sets us apart from competitors, but also paves the way for lucrative investment opportunities in the New Zealand property market.
Feel free to use any images from www.kestreldwellings.co.nz
Target Market(s)
investors for a unique property development opportunity
Industry/Entity Type
luxury property development in unique locations throughout New Zealand
Colors
Designer to choose only greyscale colors for use in the design.
Look and feel

```html
<!DOCTYPE html>
<html lang="en">
<head>
<meta charset="utf-8">
<title>Kestrel – Sales Brochure</title>
<link href="https://fonts.googleapis.com/css2?family=Outfit:wght@300;400;500&display=swap" rel="stylesheet">
<style>
  :root {
    --canvas: #dcd4cb;
    --cover-grey: #686868;
    --page-dark: #717171;
    --page-light: #ebecec;
    --accent-gold: #c8b06a;
    --ink-dark: #3d3d3d;
    --ink-light: #ffffff;
    --photo-warm-a: #b9b1a6;
    --photo-warm-b: #7f7a72;
    --photo-green-a: #a9ae95;
    --photo-green-b: #5d6650;
    --photo-sea-a: #c9c6c3;
    --photo-sea-b: #6e6258;
  }
  * { box-sizing: border-box; margin: 0; padding: 0; }
  html, body {
    width: 1200px; height: 800px; overflow: hidden;
    background: var(--canvas);
    font-family: "Outfit", sans-serif;
  }
  .brochure {
    position: absolute; top: 150px; left: 50px;
    display: flex; gap: 40px;
  }
  .page {
    position: relative;
    width: 352px; height: 500px;
    overflow: hidden;
  }
  .spread { display: flex; box-shadow: 0 10px 30px rgba(0,0,0,.18); }
  .cover { box-shadow: 0 10px 30px rgba(0,0,0,.18); }

  /* Cover */
  .cover { background: var(--cover-grey); }
  .cover__photo {
    position: absolute; top: 46px; left: 20px; right: 20px; bottom: 20px;
    background: linear-gradient(160deg, var(--photo-warm-a) 0%, #d6d1c8 40%, var(--photo-warm-b) 100%);
  }
  .cover__wordmark {
    position: absolute; top: 18px; left: 22px;
    font-weight: 500; font-size: 92px; line-height: 1;
    color: var(--ink-light); letter-spacing: -3px;
  }
  .cover__tagline {
    position: absolute; left: 38px; bottom: 38px; width: 200px;
    font-weight: 300; font-size: 11px; line-height: 1.35; color: var(--ink-light);
  }
  .cover__brand {
    position: absolute; right: 36px; bottom: 40px;
    display: flex; align-items: center; gap: 6px;
    color: var(--ink-light); font-weight: 400; font-size: 11px;
  }
  .cover__brand-mark { width: 8px; height: 8px; background: var(--ink-light); }
  .cover__brand-sub {
    display: block; font-size: 6.5px; line-height: 1.2; font-weight: 400;
  }

  /* Inside left */
  .about { background: var(--page-dark); color: var(--ink-light); padding: 40px 26px 0; }
  .rule { width: 42px; height: 2px; background: var(--ink-light); margin-bottom: 12px; }
  .section-title {
    color: var(--accent-gold); font-weight: 300; font-size: 15px; margin-bottom: 12px;
  }
  .body-copy { font-weight: 300; font-size: 7.4px; line-height: 1.5; margin-bottom: 7px; }
  .about__photo {
    position: absolute; left: 34px; right: 26px; top: 200px; height: 230px;
    background: linear-gradient(170deg, var(--photo-green-a) 0%, #cfd0c2 35%, var(--photo-green-b) 100%);
    outline: 1px solid var(--accent-gold); outline-offset: 3px;
  }
  .caption { font-weight: 300; font-size: 6.5px; }
  .about__caption { position: absolute; right: 26px; top: 442px; color: var(--ink-light); }

  /* Inside right */
  .approach { background: var(--page-light); color: var(--ink-dark); padding: 26px 26px 0; }
  .approach__head { display: flex; align-items: center; gap: 14px; margin-bottom: 16px; }
  .approach__brand { font-weight: 500; font-size: 15px; color: var(--ink-dark); }
  .approach__headline { font-weight: 300; font-size: 11px; line-height: 1.3; }
  .approach__photo {
    height: 200px;
    background: linear-gradient(180deg, var(--photo-sea-a) 0%, #a9a8a8 45%, var(--photo-sea-b) 100%);
  }
  .approach__caption { text-align: right; margin: 6px 0 22px; font-style: italic; }
  .approach .rule { background: #9a9a9a; width: 60px; }
  .columns { display: flex; gap: 14px; }
  .columns > div { flex: 1; }
  .approach__footer {
    position: absolute; right: 26px; bottom: 18px;
    display: flex; gap: 14px; font-size: 6.5px; font-weight: 400;
  }
</style>
</head>
<body>
  <main class="brochure">
    <section class="page cover">
      <div class="cover__photo" role="img" aria-label="Photo of a bedroom with floor-to-ceiling glass corner windows opening to a garden"></div>
      <h1 class="cover__wordmark">Kestrel</h1>
      <p class="cover__tagline">Architecturally designed, thoughtfully constructed, and delivered anywhere throughout New Zealand</p>
      <div class="cover__brand">
        <span class="cover__brand-mark"></span>
        <span>Kestrel<span class="cover__brand-sub">Modular Architectural Homes</span></span>
      </div>
    </section>

    <div class="spread">
      <section class="page about">
        <div class="rule"></div>
        <h2 class="section-title">About us</h2>
        <p class="body-copy">Kestrel Dwellings Developments is an emerging New Zealand property investment company with a focus on providing unique property investment opportunities.</p>
        <p class="body-copy">Our expertise and capabilities in architectural modular homes provide us with a remarkable advantage in tackling the development of properties that are typically considered challenging, remote, or uniquely positioned.</p>
        <div class="about__photo" role="img" aria-label="Photo of a modern home with glass walls set among trees and lawn"></div>
        <p class="caption about__caption">Bespoke Multi Level No. 1</p>
      </section>

      <section class="page approach">
        <header class="approach__head">
          <span class="approach__brand">Kestrel</span>
          <p class="approach__headline">Modular, architectural homes<br>with flexibility and sophistication</p>
        </header>
        <div class="approach__photo" role="img" aria-label="Photo of a living room with a large corner window looking out to the sea"></div>
        <p class="caption approach__caption">The Designer Series No. 2</p>
        <div class="rule"></div>
        <h2 class="section-title">Our unique approach</h2>
        <div class="columns">
          <div>
            <p class="body-copy">Architecturally-designed, highly customisable homes, built off-site, delivered to and assembled on a plot of land anywhere in New Zealand.</p>
            <p class="body-copy">At Kestrel, our aim is to help people envision their own homes; to simplify the process of crafting and building them to exacting standards; and give our customers and their families personalised homes in which to forge memories of shelter and comfort.</p>
          </div>
          <div>
            <p class="body-copy">Our manufacturing processes have been tried, perfected and are independent of weather or site constraints, allowing for an orderly, systematic building phase and rapid turnaround times.</p>
            <p class="body-copy">By delivering prefabricated and ready-to-assemble components to your site, we minimise the number of workers, tools, vehicles and time required on site.</p>
          </div>
        </div>
        <footer class="approach__footer"><span>Sell the dream!</span><span>3</span></footer>
      </section>
    </div>
  </main>
</body>
</html>
```